Dietitian needs awesome business card

I need a contemporary design that's eye catching but professional.
My card is to given to doctors, specialists and patients alike.
I manage patients with chronic diseases
I have uploaded my logo and current business card, I would also like the other Certified Clinical Nutritionist logo incorporated into the design

Target Market(s)

Doctors, specialists and patients

Industry/Entity Type

Healthcare

Contact Information for Business Card

www.brightfieldnutrition.com.au
Ph: 0427 561 903
Fax: 6457 2183
email: marcus.k.diet@fernmail.com
Space on the back of the card with: Appointment date, Appointment time and appointment location

Font styles to use
Serif

Colors
fbee3e
876aae
ffc214

Requirements
Must have
• My Logo
• Certified Clinical Nutritionist Logo
• My 4 locations - Pinebrook Medical Centre, North Corrin Health, Hollis Medical, Ashcombe Doctors Surgery
Nice to have
• I like the colours in my current business card

```html
<!DOCTYPE html>
<html lang="en">
<head>
<meta charset="utf-8">
<title>Brightfield Nutrition &amp; Dietetics – Business Card</title>
<link rel="stylesheet" href="https://fonts.googleapis.com/css2?family=Open+Sans:wght@300;400;700&family=Crimson+Text:ital@1&display=swap">
<style>
  :root {
    --bg: #ecebe8;
    --card: #ffffff;
    --blue: #1a9fd8;
    --blue-deep: #1f5fae;
    --blue-light: #25b4e6;
    --navy: #2b4f9c;
    --green: #8cc63f;
    --orange: #f08a2c;
    --line: #3a5ea8;
  }
  * { box-sizing: border-box; margin: 0; padding: 0; }
  html, body { width: 1200px; height: 1023px; overflow: hidden; }
  body { background: var(--bg); font-family: "Open Sans", sans-serif; position: relative; }

  .card {
    position: absolute; left: 220px; width: 760px; height: 435px;
    background: var(--card); border-radius: 16px; overflow: hidden;
    box-shadow: 0 6px 18px rgba(0,0,0,.18);
  }
  .card--front { top: 50px; }
  .card--back { top: 530px; }

  .front__field {
    position: absolute; right: 0; top: 0; bottom: 0; width: 300px;
    background: linear-gradient(200deg, var(--blue-light), var(--blue) 45%, var(--blue-deep));
  }

  .brand { display: flex; align-items: center; gap: 14px; }
  .brand__dot { border-radius: 50%; flex: none; }
  .brand__name { font-weight: 300; line-height: 1; }
  .brand__sub { font-weight: 300; line-height: 1.2; }

  .card--front .brand { position: absolute; left: 48px; top: 110px; }
  .card--front .brand__dot { background: var(--navy); width: 54px; height: 54px; }
  .card--front .brand__name { font-size: 56px; color: var(--navy); }
  .card--front .brand__sub { font-size: 21px; color: var(--navy); margin-top: 4px; }

  .person { position: absolute; left: 116px; top: 270px; }
  .person__name { font-size: 28px; font-weight: 700; color: var(--navy); }
  .person__title { font-size: 15px; color: var(--green); margin-top: 2px; }

  .contact { position: absolute; right: 36px; top: 60px; color: #fff; }
  .contact__row { display: flex; align-items: center; justify-content: flex-end; gap: 10px; font-size: 18px; margin-bottom: 8px; }
  .contact__icon { width: 18px; height: 18px; }
  .badge { position: absolute; right: 36px; top: 150px; width: 66px; height: 66px; background: var(--orange); border-radius: 4px; }
  .contact__web { position: absolute; right: 24px; bottom: 48px; color: #fff; font-size: 15px; }

  .back__strip { position: absolute; left: 0; top: 0; bottom: 0; width: 22px; background: var(--blue); }
  .back__panel {
    position: absolute; right: 0; top: 0; bottom: 0; width: 300px;
    background: linear-gradient(160deg, var(--blue-light), var(--blue) 55%, #137bbf);
    display: flex; align-items: center; justify-content: center;
  }
  .back__panel .brand { gap: 12px; }
  .back__panel .brand__dot { background: #fff; width: 40px; height: 40px; }
  .back__panel .brand__name { font-size: 40px; color: #fff; }
  .back__panel .brand__sub { font-size: 15px; color: #fff; margin-top: 3px; }

  .appointment { position: absolute; left: 60px; top: 40px; width: 380px; }
  .appointment__title { font-family: "Crimson Text", serif; font-style: italic; font-size: 34px; color: var(--blue); text-align: center; margin-bottom: 30px; }
  .field { display: flex; align-items: flex-end; gap: 10px; border-bottom: 1px solid var(--line); height: 66px; padding-bottom: 4px;
    font-family: "Crimson Text", serif; font-style: italic; font-size: 17px; color: var(--navy); }
  .field__gap { flex: 1; }
</style>
</head>
<body>

<section class="card card--front" aria-label="Business card front">
  <div class="front__field" role="img" aria-label="Blue and green decorative wave area"></div>

  <div class="brand">
    <span class="brand__dot"></span>
    <div>
      <div class="brand__name">Brightfield</div>
      <div class="brand__sub">Nutrition &amp; Dietetics</div>
    </div>
  </div>

  <div class="person">
    <div class="person__name">Marcus Kellaway</div>
    <div class="person__title">Certified Clinical Nutritionist</div>
  </div>

  <div class="contact">
    <div class="contact__row">0427 561 903
      <svg class="contact__icon" viewBox="0 0 20 20" aria-hidden="true"><circle cx="10" cy="10" r="8.5" fill="none" stroke="#fff" stroke-width="1.5"/><path d="M7 5.5l1.8 2-1 1.4c.7 1.4 1.6 2.3 3 3l1.4-1 2 1.8-1.2 1.5c-3.4-.4-6.2-3.2-6.6-6.6z" fill="#fff"/></svg>
    </div>
    <div class="contact__row">6457 2183
      <svg class="contact__icon" viewBox="0 0 20 20" aria-hidden="true"><rect x="4" y="3" width="12" height="14" rx="1.5" fill="#fff"/><rect x="6" y="6" width="8" height="1.5" fill="#1a9fd8"/><rect x="6" y="9" width="8" height="1.5" fill="#1a9fd8"/></svg>
    </div>
  </div>
  <div class="badge" aria-label="Accreditation badge"></div>
  <div class="contact__web">www.brightfieldnutrition.com.au</div>
</section>

<section class="card card--back" aria-label="Appointment card back">
  <div class="back__strip"></div>
  <div class="appointment">
    <div class="appointment__title">Appointment</div>
    <div class="field">Name</div>
    <div class="field">Appointment date</div>
    <div class="field">Appointment Location<span class="field__gap"></span>Time</div>
  </div>
  <div class="back__panel">
    <div class="brand">
      <span class="brand__dot"></span>
      <div>
        <div class="brand__name">Brightfield</div>
        <div class="brand__sub">Nutrition &amp; Dietetics</div>
      </div>
    </div>
  </div>
</section>

</body>
</html>
```